Theatre Company needs poster for a Christmas show.

We need a poster for an annual Christmas musical show call "The Frosted Hour". The style is Jazzy/Lounge Christmas songs. The poster should be a mid-centry modern, Pale Ledger-style design. I have attached the past year's poster for reference. The poster should include "Brindlewood Performance Circle presents The Frosted Hour" the date "December 18th, 2015" our phone number "512-634-2817 ext 204" and our website "brindlewood-stage.org". The poster should also include the logos of our title sponsors (attached).

Target Market(s)

Lakeway, Texas residents, Adults, 21+

Industry/Entity Type

It Company

Font styles to use
Sans Serif

Requirements
Must have
• Brindlewood logo
• Show title "The Frosted Hour"
• Date: December 18th, 2015
• Phone number: 512-634-2817 ext 204
• Web site: brindlewood-stage.org
• Sponsor logos at the bottom (attached)
• Mid-century modern, Pale Ledger-style design
• Christmas/Winter colors
Nice to have
• Singer/piano/microphone imagery
• cocktail imagery

```html
<!DOCTYPE html>
<html lang="en">
<head>
<meta charset="utf-8">
<title>The Frosted Hour — Brindlewood Performance Circle</title>
<link rel="stylesheet" href="https://fonts.googleapis.com/css2?family=Great+Vibes&family=Cinzel:wght@700&display=swap">
<style>
  :root {
    --plum-deep: #2a0a2e;
    --plum: #5a1140;
    --wine: #8e1a3a;
    --ember: #e0502a;
    --gold-glow: #f5a04a;
    --magenta: #e23aa0;
    --white: #ffffff;
    --band-purple: #4a1048;
    --sponsor-ink: #3b0f3c;
  }
  * { margin: 0; padding: 0; box-sizing: border-box; }
  html, body { width: 849px; height: 1200px; overflow: hidden; background: var(--plum-deep); }
  .poster {
    position: relative;
    width: 849px;
    height: 1200px;
    overflow: hidden;
    background:
      radial-gradient(ellipse 520px 620px at 700px 420px, rgba(245,160,74,0.55), transparent 70%),
      radial-gradient(ellipse 700px 800px at 620px 500px, var(--ember), transparent 75%),
      linear-gradient(115deg, var(--plum-deep) 0%, var(--plum) 35%, var(--wine) 65%, var(--ember) 100%);
    font-family: "Cinzel", serif;
    color: var(--white);
  }
  .ornaments-art {
    position: absolute;
    left: 0; top: 0;
    width: 320px; height: 760px;
    background: linear-gradient(180deg, rgba(255,255,255,0.18), rgba(226,58,160,0.12) 60%, transparent);
  }
  .microphone-art {
    position: absolute;
    left: 300px; top: 40px;
    width: 420px; height: 560px;
    border-radius: 200px 200px 40px 40px;
    background: radial-gradient(ellipse at 45% 35%, #f4d6e0 0%, #c7708a 35%, #6a1d3f 75%, transparent 100%);
    opacity: 0.85;
  }
  .brand {
    position: absolute;
    right: 40px; top: 18px;
    display: flex; align-items: center; gap: 10px;
    font-size: 30px;
    color: var(--white);
  }
  .brand-dot { width: 14px; height: 14px; border-radius: 50%; background: var(--white); }
  .title {
    position: absolute;
    left: 330px; top: 520px;
    width: 440px;
    font-family: "Great Vibes", cursive;
    line-height: 0.9;
    text-align: center;
  }
  .title-the { display: block; font-size: 110px; color: var(--magenta); text-align: left; padding-left: 30px; }
  .title-frosted { display: block; font-size: 150px; color: var(--white); }
  .title-hour { display: block; font-size: 110px; color: var(--magenta); }
  .details {
    position: absolute;
    left: 270px; top: 865px;
    width: 520px;
    text-align: center;
  }
  .date { font-size: 44px; }
  .date sup { font-size: 24px; }
  .phone { font-size: 25px; margin-top: 10px; }
  .web { font-size: 21px; margin-top: 8px; }
  .band-trim {
    position: absolute;
    left: 0; top: 1022px;
    width: 849px; height: 26px;
    background: var(--band-purple);
    border-top: 2px solid var(--magenta);
  }
  .sponsors {
    position: absolute;
    left: 0; top: 1048px;
    width: 849px; height: 152px;
    background: var(--white);
    display: flex; align-items: center; justify-content: space-around;
    padding: 0 20px;
  }
  .sponsor {
    font-size: 22px;
    color: var(--sponsor-ink);
    text-align: center;
    max-width: 190px;
    line-height: 1.15;
  }
</style>
</head>
<body>
  <main class="poster">
    <div class="ornaments-art" role="img" aria-label="Hanging filigree Christmas baubles with snowflakes and sparkles"></div>
    <div class="microphone-art" role="img" aria-label="Glossy vintage chrome microphone glowing against warm bokeh lights"></div>

    <div class="brand"><span class="brand-dot"></span>Brindlewood</div>

    <h1 class="title">
      <span class="title-the">The</span>
      <span class="title-frosted">Frosted</span>
      <span class="title-hour">Hour</span>
    </h1>

    <section class="details">
      <p class="date">December 18<sup>th</sup>, 2015</p>
      <p class="phone">512-634-2817 ext 204</p>
      <p class="web">www.brindlewood-stage.org</p>
    </section>

    <div class="band-trim"></div>
    <footer class="sponsors">
      <span class="sponsor">Northstar Grill</span>
      <span class="sponsor">Step Studio</span>
      <span class="sponsor">Larkfield</span>
      <span class="sponsor">Mira Lens Photography</span>
    </footer>
  </main>
</body>
</html>
```